Provide bookkeeping and accounting services to small and growing businesses

We need website and logo design using the name Dornaby as the logo.
The target audience are small companies and startups who need:
1) Simple bookkeeping services
2) Accounting advice that only someone with many years of senior financial experience as a CPA can provide.

The services are provided by two individuals. each of whom specialize in one of the areas.

We want the website to be clean without a lot of visual distraction but don't know how to make a boring subject interesting. We believe our potential clients, small business owners, need to find what they want quickly and easily without a lot of verbiage or distractions.

We've attached a draft of the homepage and have completed the text on most of the other pages.

Target Market(s)

small and early stage growth companies in San Diego North County

Industry/Entity Type

Accounting

Number of Pages Required

1 page

Font styles to use
Sans Serif

Colors
86cfc6
33b8a4
85cae6

Requirements
Must have
• We need a design for the website homepage that includes the name Dornaby as the logo. Must include a design for the name.
• Must have color in teal or greenish blue.
Nice to have
• White background, clean, clear, uncluttered.
• We would like to use the design in a Theme on a WordPress website. Themes Paper Lantern and Quiet Harbour are appealing to us.
Should not have
• Moving pictures

```html
<!DOCTYPE html>
<html lang="en">
<head>
<meta charset="utf-8">
<title>Dornaby Accounting &amp; Bookkeeping</title>
<link rel="stylesheet" href="https://fonts.googleapis.com/css2?family=Dosis:wght@300;400;500&family=Lato:wght@400;700&display=swap">
<style>
:root{
  --teal:#5cc3b6;
  --teal-light:#86cfc6;
  --teal-deep:#33b8a4;
  --ink:#2b2b2b;
  --muted:#6a6a6a;
  --nav:#e5e5e5;
  --footer:#ececec;
  --social:#555;
}
*{box-sizing:border-box;margin:0;padding:0}
html,body{width:903px;height:1200px;overflow:hidden;background:#fff}
body{position:relative;font-family:"Lato",sans-serif;color:var(--ink)}
.abs{position:absolute}
.display{font-family:"Dosis",sans-serif;font-weight:300;text-transform:uppercase;letter-spacing:.3px}

/* brand */
.brand-dot{width:12px;height:12px;border-radius:50%;background:var(--teal)}
.brand-name{font-family:"Dosis",sans-serif;font-weight:400;font-size:20px;color:var(--ink);letter-spacing:.5px}
.brand-divider{width:1px;height:30px;background:#d0d0d0}
.brand-tag{font-family:"Dosis",sans-serif;font-weight:400;font-size:14px;line-height:17px;color:var(--ink);letter-spacing:.6px}

.contact-item{top:24px;height:30px;display:flex;align-items:center;gap:8px;font-size:11.5px;color:#444}
.contact-item svg{flex:none}

/* nav */
.nav{left:0;top:82px;width:903px;height:35px;background:var(--nav)}
.nav a{position:absolute;top:0;height:35px;line-height:35px;font-family:"Dosis",sans-serif;font-size:12px;color:#555;text-decoration:none;letter-spacing:.4px}
.nav a.current{background:#fff;padding:0 12px;color:#333}

/* hero */
.hero{left:0;top:117px;width:903px;height:368px;background:radial-gradient(ellipse at 45% 45%,#7b6b58 0%,#4b3f33 45%,#2a241f 100%)}
.hero-title{left:54px;top:280px;font-size:19px;line-height:22px;color:#fff}

.consult{left:598px;top:130px;width:249px;height:342px;background:#fff;border:3px solid var(--teal-light);border-top:none}
.consult-head{left:598px;top:130px;width:249px;height:65px;background:var(--teal-light)}
.consult-title{left:654px;top:144px;font-size:19px;line-height:19px;color:#fff}
.field{left:611px;width:209px;height:24px;border:1px solid #cfcfcf;font-size:11px;color:#999;padding:4px 8px}
.field.area{height:86px;line-height:14px}
.submit{left:612px;top:432px;width:62px;height:23px;background:var(--teal-light);color:#fff;font-family:"Dosis",sans-serif;font-weight:500;font-size:11px;text-align:center;line-height:23px;letter-spacing:.5px}

/* welcome */
.welcome-title{left:0;top:523px;width:903px;text-align:center;font-size:19px;line-height:20px;color:var(--ink)}
.welcome-title .accent{color:var(--teal)}
.welcome-text{left:126px;top:574px;width:651px;text-align:center;font-size:11.3px;line-height:19.5px;color:var(--muted)}
.btn-outline{left:417px;top:648px;width:69px;height:22px;border:1px solid var(--teal);color:var(--teal);font-family:"Dosis",sans-serif;font-weight:500;font-size:9.5px;text-align:center;line-height:20px;letter-spacing:.3px}

/* services */
.svc-bg{top:704px;width:452px;height:299px}
.svc-acct{left:0;background:linear-gradient(135deg,#16625d 0%,#1e7a72 55%,#155b56 100%)}
.svc-book{left:452px;width:451px;background:linear-gradient(135deg,#1b5267 0%,#23657d 50%,#1a4f63 100%)}
.svc-ring{width:50px;height:50px;border:2px solid var(--teal-light);border-radius:50%;display:flex;align-items:center;justify-content:center}
.svc-title{font-size:19px;line-height:20px;color:#fff}
.svc-list{list-style:none;font-size:11.3px;color:#fff}
.svc-list li{height:21px;line-height:16px;display:flex;gap:6px;align-items:flex-start}
.svc-list li::before{content:"";width:6px;height:6px;border:1.2px solid #fff;border-radius:50%;margin-top:4px;flex:none}
.btn-light{width:70px;height:22px;border:1px solid #fff;color:#fff;font-family:"Dosis",sans-serif;font-weight:500;font-size:9.5px;text-align:center;line-height:20px}

/* footer */
.footer{left:0;top:1006px;width:903px;height:194px;background:var(--footer);border-top:4px solid #e0e0e0}
.foot-head{top:1035px;font-size:12.5px;font-weight:700;color:#444}
.foot-links{left:55px;top:1063px;list-style:none;font-size:10px;color:#555}
.foot-links li{height:17px}
.touch-icon{left:190px;width:26px;height:26px;border-radius:50%;background:#555;display:flex;align-items:center;justify-content:center}
.touch-text{left:226px;font-size:10px;line-height:17px;color:#555}
.social-box{left:394px;width:26px;height:26px;background:var(--social);display:flex;align-items:center;justify-content:center}
.social-name{left:428px;font-size:10px;color:#555}
.legal{right:55px;top:1142px;text-align:right;font-size:9.5px;line-height:14px;color:#555}
</style>
</head>
<body>

<header>
  <div class="abs brand-dot" style="left:56px;top:35px"></div>
  <div class="abs brand-name" style="left:76px;top:28px">DORNABY</div>
  <div class="abs brand-divider" style="left:166px;top:26px"></div>
  <div class="abs brand-tag" style="left:181px;top:24px">ACCOUNTING &amp;<br>BOOKKEEPING</div>

  <div class="abs contact-item" style="left:572px">
    <svg width="30" height="30" viewBox="0 0 30 30"><circle cx="15" cy="15" r="14" fill="none" stroke="#5cc3b6" stroke-width="1.5"/><path d="M10 9c1-1 2-1 2.5 0l1.2 2.3c.3.6 0 1.2-.5 1.5l-.7.5c.8 1.8 2 3 3.7 3.8l.5-.7c.4-.5 1-.7 1.5-.4l2.3 1.2c.9.5.9 1.5 0 2.4-1.5 1.5-4 .8-6.6-1.8S8.5 10.5 10 9z" fill="none" stroke="#777" stroke-width="1"/></svg>
    <span>1800 555 0142</span>
  </div>
  <div class="abs contact-item" style="left:709px">
    <svg width="30" height="30" viewBox="0 0 30 30"><circle cx="15" cy="15" r="14" fill="none" stroke="#5cc3b6" stroke-width="1.5"/><rect x="9" y="10.5" width="13" height="9" fill="none" stroke="#777" stroke-width="1"/><path d="M9 10.5l6.5 5 6.5-5" fill="none" stroke="#777" stroke-width="1"/></svg>
    <span>info@dornaby.com</span>
  </div>
</header>

<nav class="abs nav">
  <a class="current" style="left:56px">HOME</a>
  <a style="left:125px">ABOUT US</a>
  <a style="left:204px">SERVICES</a>
  <a style="left:278px">EXPERIENCE</a>
  <a style="left:367px">RESOURCES</a>
  <a style="left:455px">CONTACT US</a>
</nav>

<section>
  <div class="abs hero" role="img" aria-label="Photo of hands typing on a laptop on a wooden desk beside a tablet showing charts, pencils and a calculator"></div>
  <h1 class="abs hero-title display">We provide a full range of<br>accounting and bookkeeping services</h1>

  <div class="abs consult"></div>
  <div class="abs consult-head"></div>
  <svg class="abs" style="left:610px;top:139px" width="36" height="46" viewBox="0 0 36 46">
    <circle cx="16" cy="11" r="7" fill="none" stroke="#fff" stroke-width="1.6"/>
    <path d="M4 40v-9c0-5 4-9 9-9h6" fill="none" stroke="#fff" stroke-width="1.6"/>
    <rect x="16" y="28" width="16" height="12" fill="none" stroke="#fff" stroke-width="1.6"/>
    <line x1="2" y1="42" x2="34" y2="42" stroke="#fff" stroke-width="1.6"/>
  </svg>
  <div class="abs consult-title display">Request a<br>free consultation</div>

  <div class="abs field" style="top:209px">Full Name</div>
  <div class="abs field" style="top:240px">Email Address</div>
  <div class="abs field" style="top:270px">Company Name</div>
  <div class="abs field" style="top:301px">Phone</div>
  <div class="abs field area" style="top:331px">Anything else we should know in advance?</div>
  <div class="abs submit">SUBMIT</div>
</section>

<section>
  <h2 class="abs welcome-title display">Welcome to <span class="accent">Dornaby</span><br>Accounting &amp; Bookkeeping</h2>
  <p class="abs welcome-text">Dornaby offers a flexible range of accounting and bookkeeping services and support for small and growing organizations in San Diego North County. We provide bookkeeping services specializing in LedgerLeaf® at your offices or remotely from ours. We also provide a broad range of accounting services or financial advice.</p>
  <div class="abs btn-outline">LEARN MORE</div>
</section>

<section>
  <div class="abs svc-bg svc-acct" role="img" aria-label="Teal-toned photo of a businessman working at a desk"></div>
  <div class="abs svc-bg svc-book" role="img" aria-label="Blue-toned photo of colleagues reviewing documents around a table"></div>

  <div class="abs svc-ring" style="left:56px;top:744px">
    <svg width="26" height="26" viewBox="0 0 26 26"><rect x="11" y="8" width="11" height="15" fill="none" stroke="#fff" stroke-width="1.4"/><rect x="13" y="10" width="7" height="3" fill="#fff"/><path d="M14 16h1M17 16h1M14 19h1M17 19h1" stroke="#fff" stroke-width="1.4"/><path d="M4 5l4-2 3 6-3 2" fill="none" stroke="#fff" stroke-width="1.4"/></svg>
  </div>
  <h3 class="abs svc-title display" style="left:120px;top:750px">Accounting<br>services</h3>
  <ul class="abs svc-list" style="left:120px;top:812px">
    <li>Accounts payable</li>
    <li>Billing and accounts receivable</li>
    <li>Financial statement preparation</li>
    <li>Payroll services</li>
    <li>Daily deposit verification</li>
  </ul>
  <div class="abs btn-light" style="left:120px;top:931px">LEARN MORE</div>

  <div class="abs svc-ring" style="left:508px;top:744px">
    <svg width="26" height="26" viewBox="0 0 26 26"><rect x="3" y="5" width="6" height="16" fill="none" stroke="#fff" stroke-width="1.4"/><rect x="10" y="5" width="6" height="16" fill="none" stroke="#fff" stroke-width="1.4"/><rect x="17" y="5" width="6" height="16" fill="none" stroke="#fff" stroke-width="1.4"/><circle cx="6" cy="17" r="1" fill="#fff"/><circle cx="13" cy="17" r="1" fill="#fff"/><circle cx="20" cy="17" r="1" fill="#fff"/></svg>
  </div>
  <h3 class="abs svc-title display" style="left:571px;top:750px">Bookkeeping<br>services</h3>
  <ul class="abs svc-list" style="left:571px;top:812px">
    <li>Bank Reconciliation Reports</li>
    <li>Budgeting Cash Flow Statement</li>
    <li>Create Collections Process</li>
    <li>Record Payments</li>
    <li>Financial Dashboard</li>
  </ul>
  <div class="abs btn-light" style="left:571px;top:931px">LEARN MORE</div>
</section>

<footer>
  <div class="abs footer"></div>

  <h4 class="abs foot-head" style="left:55px">Quick Links</h4>
  <ul class="abs foot-links">
    <li>Home</li><li>About Us</li><li>Services</li><li>Experience</li><li>Resources</li><li>Contact Us</li>
  </ul>

  <h4 class="abs foot-head" style="left:190px">Get In Touch</h4>
  <div class="abs touch-icon" style="top:1065px"><svg width="12" height="14" viewBox="0 0 12 14"><path d="M6 13S1 8 1 5a5 5 0 0110 0c0 3-5 8-5 8z" fill="#fff"/><circle cx="6" cy="5" r="1.8" fill="#555"/></svg></div>
  <div class="abs touch-text" style="top:1062px">14 Harbor Lane, Suite 3,<br>Oceanview 92024</div>
  <div class="abs touch-icon" style="top:1104px"><svg width="12" height="12" viewBox="0 0 12 12"><path d="M2 1c.7-.7 1.4-.7 1.8 0l.9 1.7c.2.4 0 .8-.3 1l-.5.4c.6 1.3 1.5 2.2 2.7 2.8l.4-.5c.3-.3.7-.5 1-.3l1.8.9c.7.4.7 1.1 0 1.8C8.7 11.9 6.8 11.4 4.7 9.3S.9 2.1 2 1z" fill="#fff"/></svg></div>
  <div class="abs touch-text" style="top:1101px">Call Us:<br>1800 555 0142</div>
  <div class="abs touch-icon" style="top:1143px"><svg width="12" height="10" viewBox="0 0 12 10"><rect x="0.5" y="0.5" width="11" height="9" fill="#fff"/><path d="M.5 .5l5.5 4.5 5.5-4.5" fill="none" stroke="#555" stroke-width="1"/></svg></div>
  <div class="abs touch-text" style="top:1141px">Email Us:<br>info@dornaby.com</div>

  <h4 class="abs foot-head" style="left:394px">Connect With Us</h4>
  <div class="abs social-box" style="top:1065px"><svg width="14" height="14" viewBox="0 0 14 14"><path d="M4 7l6-3.5M4 7l6 3.5" stroke="#fff" stroke-width="1.2"/><circle cx="3.5" cy="7" r="2" fill="#fff"/><circle cx="10.5" cy="3.2" r="2" fill="#fff"/><circle cx="10.5" cy="10.8" r="2" fill="#fff"/></svg></div>
  <div class="abs social-name" style="top:1072px">Circlebook</div>
  <div class="abs social-box" style="top:1097px"><svg width="14" height="14" viewBox="0 0 14 14"><path d="M4 7l6-3.5M4 7l6 3.5" stroke="#fff" stroke-width="1.2"/><circle cx="3.5" cy="7" r="2" fill="#fff"/><circle cx="10.5" cy="3.2" r="2" fill="#fff"/><circle cx="10.5" cy="10.8" r="2" fill="#fff"/></svg></div>
  <div class="abs social-name" style="top:1104px">Chirper</div>
  <div class="abs social-box" style="top:1130px"><svg width="14" height="14" viewBox="0 0 14 14"><path d="M4 7l6-3.5M4 7l6 3.5" stroke="#fff" stroke-width="1.2"/><circle cx="3.5" cy="7" r="2" fill="#fff"/><circle cx="10.5" cy="3.2" r="2" fill="#fff"/><circle cx="10.5" cy="10.8" r="2" fill="#fff"/></svg></div>
  <div class="abs social-name" style="top:1137px">Linkfolio</div>

  <div class="abs brand-dot" style="left:620px;top:1064px"></div>
  <div class="abs brand-name" style="left:640px;top:1057px">DORNABY</div>
  <div class="abs brand-divider" style="left:727px;top:1053px;background:#fff"></div>
  <div class="abs brand-tag" style="left:743px;top:1051px;color:#444">ACCOUNTING &amp;<br>BOOKKEEPING</div>

  <div class="abs legal">© 2016 Dornaby Accounting &amp; Bookkeeping<br>Privacy Policy | Terms of Use | Sitemap</div>
</footer>

</body>
</html>
```